Home Remodeling company needs a business card design

we need a business card design for home remodeling company in hamilton county, indiana USA. we offers a wide range of construction services including whole house renovations, Design and Build Basements and Kitchen and Bathroom Remodeling . we would like to see designs for both site of business card that use the same color of the company logo and also including all information below :
1- Karim Feltous CEO / General Contractor
2- all company contacts Telephone numbers ( 1-888-DULOM-47 ) ( 317-555-0193) email address ( info@dulomhome.com) website ( www.dulomhome.com ) and social media logos (Facebook- twitter- google plus )
3- company logo
4- licensed . insured . bonded

```html
<!DOCTYPE html>
<html lang="en">
<head>
<meta charset="utf-8">
<title>Dulom Home Remodeling – Business Card</title>
<link rel="stylesheet" href="https://fonts.googleapis.com/css2?family=Open+Sans:wght@400;600&family=Lora:wght@400&display=swap">
<style>
  :root {
    --backdrop: #e9e6e1;
    --card: #ffffff;
    --ink: #4a4a4c;
    --ink-soft: #6a6a6c;
    --brand-red: #cc2a3c;
    --band-grey: #bdbdbf;
    --band-grey-light: #d2d2d4;
  }
  * { margin: 0; padding: 0; box-sizing: border-box; }
  html, body {
    width: 1200px; height: 892px; overflow: hidden;
    background: var(--backdrop);
  }
  .canvas { position: relative; width: 1200px; height: 892px; }
  .card {
    position: absolute; top: 297px;
    width: 520px; height: 297px;
    background: var(--card);
    overflow: hidden;
    box-shadow: 0 6px 18px rgba(0,0,0,0.18);
  }
  .card--front { left: 40px; }
  .card--back { left: 640px; }

  /* Company name placeholder */
  .brand-name {
    position: absolute; display: flex; align-items: center;
    font-family: "Open Sans", sans-serif; font-weight: 600;
    color: var(--ink); white-space: nowrap;
  }
  .brand-name__mark { background: var(--brand-red); flex: none; }

  .card--front .brand-name { left: 0; right: 0; top: 108px; justify-content: center; font-size: 30px; }
  .card--front .brand-name__mark { width: 22px; height: 22px; margin-right: 14px; }

  .credentials {
    position: absolute; left: 0; right: 0; top: 170px;
    text-align: center;
    font-family: "Open Sans", sans-serif; font-size: 13px; font-weight: 400;
    letter-spacing: 3px; text-transform: uppercase; color: var(--ink-soft);
  }
  .front-band {
    position: absolute; left: 0; right: 0; bottom: 0; height: 26px;
    background: var(--brand-red);
  }

  .card--back .brand-name { left: 230px; top: 42px; font-size: 21px; }
  .card--back .brand-name__mark { width: 15px; height: 15px; margin-right: 10px; }

  .back-shapes { position: absolute; inset: 0; }

  .contact-list {
    position: absolute; left: 24px; top: 196px;
    list-style: none;
    font-family: "Open Sans", sans-serif; font-size: 14px; color: var(--ink);
  }
  .contact-list li { display: flex; align-items: center; height: 22px; }
  .contact-icon { width: 13px; height: 13px; margin-right: 10px; flex: none; }

  .person {
    position: absolute; left: 280px; top: 146px; width: 230px; height: 50px;
    text-align: right;
    transform: rotate(6.6deg); transform-origin: center;
    display: flex; flex-direction: column; justify-content: center;
  }
  .person__name {
    font-family: "Lora", serif; font-size: 21px; color: var(--brand-red); line-height: 1.1;
  }
  .person__title {
    font-family: "Open Sans", sans-serif; font-size: 12px; color: var(--ink); line-height: 1.3;
  }

  .social-links { position: absolute; left: 390px; top: 238px; display: flex; gap: 10px; }
  .social-links span {
    width: 30px; height: 30px; border-radius: 5px;
    background: rgba(255,255,255,0.85);
  }
</style>
</head>
<body>
<main class="canvas">

  <section class="card card--front" aria-label="Business card front">
    <div class="brand-name">
      <span class="brand-name__mark"></span>
      <span>Dulom Home Remodeling</span>
    </div>
    <p class="credentials">Licensed · Insured · Bonded</p>
    <div class="front-band"></div>
  </section>

  <section class="card card--back" aria-label="Business card back">
    <svg class="back-shapes" width="520" height="297" viewBox="0 0 520 297">
      <defs>
        <linearGradient id="bandShade" x1="0" y1="0" x2="1" y2="0">
          <stop offset="0" stop-color="#d2d2d4"/>
          <stop offset="1" stop-color="#bdbdbf"/>
        </linearGradient>
      </defs>
      <polygon points="0,100 520,160 520,210 0,150" fill="url(#bandShade)"/>
      <polygon points="370,192.7 520,210 520,297 270,297" fill="#cc2a3c"/>
    </svg>

    <div class="brand-name">
      <span class="brand-name__mark"></span>
      <span>Dulom Home Remodeling</span>
    </div>

    <ul class="contact-list">
      <li>
        <svg class="contact-icon" viewBox="0 0 13 13"><rect width="13" height="13" rx="2" fill="#cc2a3c"/><path d="M4 3.2c.4-.3.9-.2 1.1.2l.6 1.2c.2.4 0 .7-.3.9l-.4.3c.4.9 1.1 1.6 2 2l.3-.4c.2-.3.6-.4.9-.2l1.2.6c.4.2.5.7.2 1.1l-.5.6c-.3.3-.8.4-1.3.2C6 9.1 4.2 7.3 3.4 5.4c-.2-.5-.1-1 .2-1.3z" fill="#fff"/></svg>
        1-888-DULOM-47
      </li>
      <li>
        <svg class="contact-icon" viewBox="0 0 13 13"><rect width="13" height="13" rx="2" fill="#cc2a3c"/><rect x="4.5" y="2.5" width="4" height="8" rx="0.8" fill="#fff"/><rect x="5.5" y="3.5" width="2" height="5" fill="#cc2a3c"/></svg>
        317-555-0193
      </li>
      <li>
        <svg class="contact-icon" viewBox="0 0 13 13"><rect width="13" height="13" rx="2" fill="#cc2a3c"/><rect x="2.5" y="4" width="8" height="5.5" fill="#fff"/><path d="M2.5 4l4 3 4-3" stroke="#cc2a3c" stroke-width="0.8" fill="none"/></svg>
        info@dulomhome.com
      </li>
      <li>
        <svg class="contact-icon" viewBox="0 0 13 13"><rect width="13" height="13" rx="2" fill="#cc2a3c"/><circle cx="6.5" cy="6.5" r="3.6" stroke="#fff" stroke-width="1" fill="none"/><path d="M2.9 6.5h7.2M6.5 2.9v7.2" stroke="#fff" stroke-width="0.8"/></svg>
        www.dulomhome.com
      </li>
    </ul>

    <div class="person">
      <span class="person__name">Karim Feltous</span>
      <span class="person__title">CEO / General Contractor</span>
    </div>

    <div class="social-links" aria-label="Social media links">
      <span></span><span></span><span></span>
    </div>
  </section>

</main>
</body>
</html>
```